Flyer for our prophetic church event

I need a flyer designed for the launching of our "7 Kindled Sabbath Gatherings" event. This event should high light the next 7 Sundays starting on February the 11th, 2018

Event Name:
7 Kindled Sabbaths

Event Slogan or topic:
Go and tell John ... the blind see, the lame walk, the lepers are cleansed, the deaf hear, the dead are raised,
the poor have the gospel preached to them.

Speaker:
Prophet Tobias Mwale

February 11th
February 18th
February 25th
March 4th
March 11th
March 18th
March 25th

Location:
Halvorn Community Center
583 Quillby Street
Portland, ME 04387
United States

Time:
10:00AM - 12:00PM

We welcome you all in the name of Jesus Christ

Contact Info:
Tel:+1(207) 555 0148 - Email:contact@brightvale-fellowship.org - Website: http://olvek.org

Target Market(s)

Young adults

Industry/Entity Type

Church

Font styles to use
Other font styles liked:
• Surprise me, I trust the designers skills

Colors

Designer to choose colors to be used in the design.

Requirements
Must have
• The Olvek logo
• Tobias Mwale's picture
• The
Should not have
• The background of the Tobias Mwale's picture

```html
<!DOCTYPE html>
<html lang="en">
<head>
<meta charset="utf-8">
<title>7 Kindled Sabbath Gatherings</title>
<link rel="stylesheet" href="https://fonts.googleapis.com/css2?family=Ubuntu:wght@400;500;700&display=swap">
<style>
  :root {
    --sky-violet: #6a4a9c;
    --sky-pink: #e7b3c9;
    --sky-orange: #f0a35c;
    --sky-light: #fbf3ee;
    --title-blue: #5aa6e0;
    --seven-purple: #8a3f9a;
    --grey-text: #8a8a92;
    --date-orange: #e58a2b;
    --item-blue: #3d95dc;
    --box-grey: #5e5e64;
    --band-purple: #a6598e;
    --band-yellow: #f5c46b;
    --white: #ffffff;
    --line-blue: #2f86d6;
    --dark-text: #555560;
  }
  * { box-sizing: border-box; margin: 0; padding: 0; }
  html, body { width: 971px; height: 1200px; overflow: hidden; background: var(--white); }
  body { font-family: "Ubuntu", sans-serif; line-height: 1.2; }
  .flyer { position: relative; width: 971px; height: 1200px; overflow: hidden; }
  .sky {
    position: absolute; inset: 0 0 212px 0;
    background:
      radial-gradient(ellipse 45% 35% at 45% 40%, var(--sky-light) 0%, rgba(251,243,238,0) 70%),
      radial-gradient(ellipse 40% 30% at 10% 55%, var(--sky-orange) 0%, rgba(240,163,92,0) 70%),
      radial-gradient(ellipse 50% 40% at 95% 15%, var(--sky-violet) 0%, rgba(106,74,156,0) 75%),
      linear-gradient(180deg, #c9a7d4 0%, var(--sky-pink) 35%, #f6e4e6 60%, #ffffff 100%);
  }
  .hero-art {
    position: absolute; left: 300px; top: 80px; width: 330px; height: 240px;
    background: linear-gradient(160deg, rgba(60,60,80,.25), rgba(255,255,255,.1));
    border-radius: 6px;
  }
  .seven {
    position: absolute; left: 250px; top: 40px; width: 380px;
    font-size: 330px; line-height: 1; font-weight: 700; text-align: center;
    color: var(--seven-purple); opacity: .85;
  }
  .title {
    position: absolute; left: 0; right: 0; top: 335px; text-align: center;
    font-size: 100px; line-height: 1; font-weight: 500; letter-spacing: 2px;
    color: var(--title-blue);
  }
  .subtitle {
    position: absolute; left: 0; right: 0; top: 433px; text-align: center;
    font-size: 40px; line-height: 1; font-weight: 400; letter-spacing: 5px; color: var(--grey-text);
  }
  .date-bar {
    position: absolute; left: 0; right: 0; top: 494px; height: 40px;
    display: flex; justify-content: center; align-items: center;
  }
  .date-bar::before, .date-bar::after {
    content: ""; position: absolute; top: 0; height: 40px; width: 270px;
    background: rgba(255,255,255,.55);
  }
  .date-bar::before { left: 0; }
  .date-bar::after { right: 0; }
  .date-text { font-size: 34px; line-height: 1; font-weight: 500; color: var(--date-orange); position: relative; }
  .date-text sup { font-size: 18px; }
  .start-tag {
    position: absolute; left: 410px; top: 482px; padding: 2px 6px;
    background: var(--item-blue); color: var(--white); font-size: 11px; font-weight: 700;
  }
  .schedule { position: absolute; left: 0; top: 0; }
  .session { position: absolute; display: flex; align-items: center; width: 225px; height: 46px; }
  .session .num {
    width: 44px; height: 46px; background: var(--box-grey); color: var(--white);
    font-size: 30px; font-weight: 700; display: flex; align-items: center; justify-content: center;
  }
  .session .info { margin-left: 8px; border-bottom: 1px solid rgba(120,120,130,.5); flex: 1; padding-bottom: 3px; }
  .session .when { font-size: 12px; color: var(--date-orange); }
  .session .topic { font-size: 17px; color: var(--item-blue); }
  .finale { position: absolute; left: 265px; top: 729px; }
  .finale .num {
    position: absolute; left: 0; top: 0; width: 64px; height: 61px;
    background: var(--box-grey); color: var(--white); font-size: 38px; font-weight: 700;
    display: flex; align-items: center; justify-content: center;
  }
  .finale .topic {
    position: absolute; left: 70px; top: 25px; width: 500px; height: 40px;
    background: var(--item-blue); color: var(--white); font-size: 21px; font-weight: 500;
    display: flex; align-items: center; padding-left: 12px; white-space: nowrap;
  }
  .finale .when {
    position: absolute; left: 430px; top: 0; width: 130px; height: 24px;
    background: var(--date-orange); color: var(--white); font-size: 15px;
    display: flex; align-items: center; justify-content: center;
  }
  .details {
    position: absolute; left: 0; right: 0; top: 843px; height: 145px;
    background: var(--band-purple); color: var(--white);
  }
  .details .label { position: absolute; font-size: 24px; font-weight: 500; color: var(--band-yellow); }
  .details .value { position: absolute; font-size: 24px; font-weight: 500; }
  .details .address { position: absolute; font-size: 15px; font-weight: 500; white-space: nowrap; }
  .speaker-photo {
    position: absolute; left: 0; top: 745px; width: 245px; height: 243px;
    background: linear-gradient(180deg, #6f6a74 0%, #2b2a30 100%);
  }
  .welcome {
    position: absolute; left: 0; right: 0; top: 1000px; text-align: center;
    font-size: 24px; line-height: 1; font-weight: 500; color: var(--date-orange);
  }
  .name-of {
    position: absolute; left: 0; right: 0; top: 1024px; text-align: center;
    font-size: 60px; line-height: 1; font-weight: 500; color: var(--line-blue);
  }
  .contact-line { position: absolute; left: 0; right: 0; top: 1092px; height: 11px; background: var(--line-blue); }
  .icon {
    position: absolute; top: 1077px; width: 40px; height: 40px; border-radius: 50%;
    background: var(--white); display: flex; align-items: center; justify-content: center;
  }
  .contact {
    position: absolute; top: 1124px; font-size: 20px; line-height: 1; color: var(--dark-text);
    text-align: center; width: 340px; white-space: nowrap;
  }
</style>
</head>
<body>
<main class="flyer">
  <div class="sky" role="img" aria-label="Glowing sky with clouds in violet, pink and orange light"></div>

  <div class="seven">7</div>
  <div class="hero-art" role="img" aria-label="Illustration of the speaker seated by the number seven with a hanging cross"></div>

  <h1 class="title">KINDLED</h1>
  <h2 class="subtitle">SABBATH GATHERINGS</h2>

  <div class="date-bar"><span class="date-text">February the 11<sup>th</sup>, 2018</span></div>
  <span class="start-tag">STARTING ON</span>

  <section class="schedule">
    <div class="session" style="left:115px;top:600px"><div class="num">1</div><div class="info"><div class="when">February 11th</div><div class="topic">Go and tell John</div></div></div>
    <div class="session" style="left:372px;top:600px"><div class="num">2</div><div class="info"><div class="when">February 18th</div><div class="topic">The blind see</div></div></div>
    <div class="session" style="left:629px;top:600px"><div class="num">3</div><div class="info"><div class="when">February 25th</div><div class="topic">The lame walk</div></div></div>
    <div class="session" style="left:115px;top:657px"><div class="num">4</div><div class="info"><div class="when">March 4th</div><div class="topic">The lepers cleansed</div></div></div>
    <div class="session" style="left:372px;top:657px"><div class="num">5</div><div class="info"><div class="when">March 11th</div><div class="topic">The deaf hear</div></div></div>
    <div class="session" style="left:629px;top:657px"><div class="num">6</div><div class="info"><div class="when">March 18th</div><div class="topic">The dead raised</div></div></div>
  </section>

  <div class="finale">
    <div class="num">7</div>
    <div class="when">March 25th</div>
    <div class="topic">The poor have the gospel preached to them.</div>
  </div>

  <section class="details">
    <span class="label" style="left:320px;top:14px">Speaker:</span>
    <span class="value" style="left:320px;top:44px">Prophet Tobias Mwale</span>
    <span class="label" style="left:660px;top:14px">Time:</span>
    <span class="value" style="left:660px;top:44px">10:00AM - 12:00PM</span>
    <span class="label" style="left:320px;top:86px">Location:</span>
    <span class="address" style="left:320px;top:117px">Halvorn Community Center , 583 Quillby Street , Portland, ME 04387 , US</span>
  </section>
  <div class="speaker-photo" role="img" aria-label="Photo of the speaker, Prophet Tobias Mwale, seated in a dark suit"></div>

  <p class="welcome">We welcome you all in the name of</p>
  <p class="name-of">Jesus Christ</p>

  <div class="contact-line"></div>
  <div class="icon" style="left:243px">
    <svg width="26" height="26" viewBox="0 0 24 24" fill="#555560"><path d="M6.6 10.8a15 15 0 0 0 6.6 6.6l2.2-2.2a1 1 0 0 1 1-.25 11.4 11.4 0 0 0 3.6.57 1 1 0 0 1 1 1V20a1 1 0 0 1-1 1A17 17 0 0 1 3 4a1 1 0 0 1 1-1h3.5a1 1 0 0 1 1 1c0 1.25.2 2.45.57 3.57a1 1 0 0 1-.25 1z"/></svg>
  </div>
  <div class="icon" style="left:532px">
    <svg width="26" height="26" viewBox="0 0 24 24" fill="none" stroke="#555560" stroke-width="2"><rect x="3" y="5" width="18" height="14"/><path d="M3 5l9 8 9-8"/></svg>
  </div>
  <div class="icon" style="left:814px">
    <svg width="26" height="26" viewBox="0 0 24 24" fill="none" stroke="#555560" stroke-width="1.8"><circle cx="12" cy="12" r="9"/><path d="M3 12h18M12 3c3 3 3 15 0 18M12 3c-3 3-3 15 0 18"/></svg>
  </div>
  <span class="contact" style="left:90px">+1(207) 555 0148</span>
  <span class="contact" style="left:382px">contact@brightvale-fellowship.org</span>
  <span class="contact" style="left:664px">http://olvek.org</span>
</main>
</body>
</html>
```